Brightmoor Leaf is a bridge for the people who drink tea to connect with the people who make the tea and the environment in which it is grown.

As a start-up, Brightmoor Leaf needs to establish a fluently persuasive brand image that articulates its unique mission to the up-market tea drinker.

Our passion for high quality tea and our respect for people are boundless. But our budget is shoe-string. Still, we will allocate a disproportionate amount to evolving a brand; including logo, labeling, and packaging, and hope this initial effort will lead to a long-term relationship with a designer. The Brightmoor label, as a component of the brand, must deny the commodity image of tea by broadcasting the uniquely flavorful, healthful, and relaxing experience of drinking tea.

The logo is an image of a liquor pouring from above into a stylized outline of a cup and gracefully folding over on itself within the cup. The image is an echo of video clips that will be featured on the Product page of the ecommerce site. Our initial thought is for the liquor and cup to be white on a rich blue background. But you may have a better idea.

The label must fit a seamless tin canister 4" in diameter; 2" high with a "window" in the lid. There are really three distinct parts to the label: a) wrap-around for the body of the tin; b) a distinct piece to be applied underneath the tin; and c) security strip (s) that connect the lid and the bottom of the tin. The wrap-around must include the following components: the logo, the brand name 'Brightmoor Leaf', the name of the specific tea and space for the following characteristics of the tea: Tea / Garden Name, Harvest Date, Tasting Notes, Weight, Location, and Caffeine content. The piece to be affixed underneath the tin should accommodate Ingredients, Brewing Instructions, and contact details for Brightmoor Leaf. The security strip(s) should be an integral part of the overall visual.

The color scheme should be expandable, i.e.; different colors for different teas.
We are thinking about rich and bold colors. But am eager to see what inspires you!

A very rough proto-type is captured in the attached files.

Target Market(s)

Ages 25 to 45 in densely populated areas of the U.S. and Canada will an above average house-hold income and an interest in what they eat / drink.

Industry/Entity Type

Environment

Requirements
Must have
• 1. Three separate pieces: 1) wrap around for the body of the tin; 2) piece to be affixed to the bottom of the body of the tin; 3) security strip (s). A word about strips: am unsure about one vs two because, two will add to overhead and processing while one will block the view of the contents. Maybe you know how to resolve.
2. clean, crisp lines
3. uncluttered
Nice to have
• 1. a color scheme to accommodate up to 30 different teas. Do not fall into the trap of incorporating the color green on the label for a 'green tea' and yellow for a lemon flavored tea. That approach is limited and has been overdone.
2. a color scheme that, as it expands to accommodate 30 teas, also is anchored by a brand color set. In other words, all labels include a recognizable color set.
3. express the level of caffeine via a gauge or metric
Should not have
• photo images,

```html
<!DOCTYPE html>
<html lang="en">
<head>
<meta charset="utf-8">
<title>Brightmoor Leaf – Tin Label Set</title>
<link rel="stylesheet" href="https://fonts.googleapis.com/css2?family=Open+Sans:wdth,wght@75,300;75,400&family=Oswald:wght@400;500;600&family=Roboto+Condensed:wght@400;700&display=swap">
<style>
  :root {
    --ink: #000000;
    --paper: #ffffff;
    --leaf-dark: #0c5a1a;
    --leaf-mid: #1f8a2e;
    --leaf-light: #4cb34a;
    --text-soft: #d9d9d9;
    --caption: #b5b5b5;
  }
  * { margin: 0; padding: 0; box-sizing: border-box; }
  html, body { width: 1200px; height: 814px; overflow: hidden; background: var(--paper); }
  body { position: relative; font-family: "Oswald", sans-serif; }

  .body-copy {
    font-family: "Open Sans", sans-serif; font-stretch: 75%; font-weight: 300;
  }

  .wrap-label { position: absolute; left: 12px; top: 17px; width: 1176px; height: 333px; overflow: hidden; }
  .wrap-label svg { display: block; }
  .wrap-title {
    position: absolute; left: 0; right: 0; top: 8px; text-align: center;
    font-family: "Oswald", sans-serif; font-weight: 500; font-size: 56px; line-height: 80px; letter-spacing: 1px;
    background: linear-gradient(#ffffff 30%, #cfcfcf 60%, #8e8e8e 90%);
    -webkit-background-clip: text; background-clip: text; color: transparent;
  }
  .wrap-variety {
    position: absolute; left: 0; right: 0; top: 272px; text-align: center;
    color: var(--paper); font-family: "Oswald", sans-serif; font-weight: 500;
    font-size: 19px; line-height: 24px; letter-spacing: 0.5px;
  }

  .base-label { position: absolute; left: 227px; top: 384px; width: 400px; height: 400px; }
  .base-mark {
    position: absolute; left: 0; right: 0; top: 40px; text-align: center;
    color: var(--paper); font-family: "Oswald", sans-serif; font-weight: 400; font-size: 14px;
  }
  .nutrition {
    position: absolute; left: 65px; top: 106px; width: 112px; height: 170px;
    background: var(--paper); color: var(--ink); padding: 3px 3px;
    font-family: "Roboto Condensed", sans-serif; font-size: 5px; line-height: 7px;
  }
  .nutrition h4 { font-family: "Roboto Condensed", sans-serif; font-weight: 700; font-size: 13px; line-height: 13px; }
  .nutrition .row { display: flex; justify-content: space-between; border-top: 0.5px solid var(--ink); }
  .nutrition .thick { border-top: 3px solid var(--ink); }
  .nutrition .indent { padding-left: 5px; }
  .nutrition b { font-weight: 700; }
  .nutrition .note { font-size: 4px; line-height: 5px; border-top: 0.5px solid var(--ink); padding-top: 1px; }

  .base-title {
    position: absolute; left: 185px; top: 104px;
    color: var(--paper); font-family: "Oswald", sans-serif; font-weight: 500; font-size: 25px; line-height: 34px;
  }
  .base-copy {
    position: absolute; left: 185px; top: 138px; width: 176px;
    color: var(--text-soft); font-size: 11.5px; line-height: 15px; text-align: justify;
  }
  .contact-icons { position: absolute; left: 188px; top: 288px; display: flex; gap: 18px; align-items: center; }
  .base-footer {
    position: absolute; left: 113px; width: 174px; top: 304px; text-align: center;
    color: var(--text-soft); font-size: 11px; line-height: 14.5px;
  }

  .security-strip {
    position: absolute; left: 750px; top: 428px; width: 109px; height: 280px;
    background: linear-gradient(90deg, var(--leaf-dark), var(--leaf-mid) 20%, var(--leaf-light) 45%, var(--leaf-mid) 70%, var(--leaf-dark));
  }
  .strip-mark {
    position: absolute; left: 0; right: 0; top: 114px; text-align: center;
    color: var(--paper); font-family: "Oswald", sans-serif; font-weight: 400; font-size: 13px; line-height: 16px;
  }
  .strip-caption {
    position: absolute; left: 750px; top: 712px; width: 109px; text-align: center;
    color: var(--caption); font-size: 15px;
  }
</style>
</head>
<body>

<section class="wrap-label">
  <svg width="1176" height="333" viewBox="0 0 1176 333">
    <defs>
      <linearGradient id="leafFill" x1="0" y1="0" x2="0" y2="1">
        <stop offset="0" stop-color="#2f9a34"/>
        <stop offset="1" stop-color="#0f6a1e"/>
      </linearGradient>
      <linearGradient id="swoosh" x1="0" y1="0" x2="0" y2="1">
        <stop offset="0" stop-color="#ffffff"/>
        <stop offset="1" stop-color="#b9b9b9"/>
      </linearGradient>
      <linearGradient id="ring" x1="0" y1="0" x2="0" y2="1">
        <stop offset="0" stop-color="#ffffff"/>
        <stop offset="1" stop-color="#9d9d9d"/>
      </linearGradient>
      <radialGradient id="badge" cx="0.5" cy="0.3" r="0.7">
        <stop offset="0" stop-color="#7cc443"/>
        <stop offset="1" stop-color="#1f8a2e"/>
      </radialGradient>
    </defs>
    <rect class="band-dark" width="1176" height="333" fill="var(--ink)"/>
    <path class="band-swoosh" d="M0,222 Q588,124 1176,222 L1176,236 Q588,136 0,236 Z" fill="url(#swoosh)"/>
    <path class="band-leaf" role="img" aria-label="Bamboo stalk pattern in green tones" d="M0,236 Q588,136 1176,236 L1176,333 L0,333 Z" fill="url(#leafFill)"/>
    <circle cx="588" cy="175" r="82" fill="url(#ring)"/>
    <circle cx="588" cy="175" r="66" fill="url(#badge)"/>
    <text x="588" y="171" text-anchor="middle" fill="#ffffff" font-family="Oswald, sans-serif" font-weight="400" font-size="17">Brightmoor</text>
    <text x="588" y="192" text-anchor="middle" fill="#ffffff" font-family="Oswald, sans-serif" font-weight="400" font-size="17">Leaf</text>
  </svg>
  <h1 class="wrap-title">BRIGHTMOOR LEAF</h1>
  <p class="wrap-variety">PURE GREEN TEA<br>500 G</p>
</section>

<section class="base-label">
  <svg width="400" height="400" viewBox="0 0 400 400">
    <defs>
      <radialGradient id="rim" cx="0.5" cy="0.5" r="0.5">
        <stop offset="0.85" stop-color="#0f6a1e"/>
        <stop offset="1" stop-color="#3aa63c"/>
      </radialGradient>
    </defs>
    <circle role="img" aria-label="Bamboo stalk border in green tones" cx="200" cy="200" r="196" fill="url(#rim)"/>
    <circle cx="200" cy="200" r="170" fill="var(--ink)"/>
  </svg>
  <p class="base-mark">Brightmoor Leaf</p>

  <div class="nutrition">
    <h4>Nutrition Facts</h4>
    <div>Serving Size 1 Tea Bag 2g (2 g)</div>
    <div>Servings per container 20</div>
    <div class="row thick"><b>Amount Per Serving</b></div>
    <div class="row"><span><b>Calories</b> 0</span><span>Calories from Fat 0</span></div>
    <div class="row thick"><span></span><b>% Daily Value*</b></div>
    <div class="row"><span><b>Total Fat</b> 0g</span><span>0%</span></div>
    <div class="row indent"><span>Saturated Fat</span><span>0%</span></div>
    <div class="row indent"><span>Trans Fat</span><span></span></div>
    <div class="row"><b>Cholesterol</b><span>0%</span></div>
    <div class="row"><span><b>Sodium</b> 1mg</span><span>0%</span></div>
    <div class="row"><b>Total Carbohydrate</b><span>0%</span></div>
    <div class="row indent"><span>Dietary Fiber</span><span>0%</span></div>
    <div class="row indent"><span>Sugars</span><span></span></div>
    <div class="row"><b>Protein</b><span></span></div>
    <div class="row thick"><span>Vitamin A 0% • Vitamin C</span><span>0%</span></div>
    <div class="row"><span>Calcium 0% • Iron</span><span>0%</span></div>
    <div class="note">*Percent Daily Values are based on a 2,000 calorie diet.</div>
  </div>

  <h2 class="base-title">BRIGHTMOOR LEAF</h2>
  <p class="base-copy body-copy">Lorem ipsum dolor sit amet, consectetur adipiscing elit. Duis condimentum non massa nec vulputate. Aliquam viverra quam id sapien aliquam, porttitor sollicitudin orci dapibus. In eget tempus nulla. In hac habitasse platea dictumst. Suspendisse porta malesuada tortor, at tincidunt purus malesuada id</p>

  <div class="contact-icons">
    <svg class="icon-phone" width="22" height="20" viewBox="0 0 22 20" role="img" aria-label="Phone">
      <path d="M2,7 Q11,0 20,7 L18,10 L15,8 L15,6 Q11,4 7,6 L7,8 L4,10 Z" fill="#ffffff"/>
      <rect x="5" y="10" width="12" height="9" rx="2" fill="#ffffff"/>
      <circle cx="11" cy="14.5" r="2.6" fill="var(--ink)"/>
    </svg>
    <svg class="icon-mail" width="22" height="16" viewBox="0 0 22 16" role="img" aria-label="Email">
      <rect x="1" y="1" width="20" height="14" fill="none" stroke="#ffffff" stroke-width="1.6"/>
      <path d="M1,1 L11,9 L21,1" fill="none" stroke="#ffffff" stroke-width="1.6"/>
    </svg>
  </div>

  <p class="base-footer body-copy">Vivamus scelerisque augue felis, non eleifend dui commodo sed. Maecenas feugiat, nibh sed vulputate porttitor, nisl quam aliquam risus,</p>
</section>

<div class="security-strip" role="img" aria-label="Bamboo stalk pattern in green tones">
  <p class="strip-mark">Brightmoor<br>Leaf</p>
</div>
<p class="strip-caption body-copy">security strip</p>

</body>
</html>
```